Design einer Kundenkarte für Handelsunternehmen
Zielgruppe
Wir sind ein Handelsunternehmen für Afro Kosmetik und für Kosmetik für Menschen mit lockigem Haar. Wir wollen eine Kundenkarte mit verschiedenen Levels herausbringen.
Aufgabenstellung
Die Kundenkarte hat verschiedene Levels für jedes Level soll ein eigenes Kartendesign entwickelt werden.
Level 1 = Lady/Sir = Ist eine kostenlose Karte, die jeder bekommen kann
Level 2 = Contessa/Conte = ist eine Karte, die an einen bestimmten Umsatz gebunden ist
Level 3 = Princes/Prince = ist eine Karte, die an einen Höheren Umsatz gebunden ist.
Level 4 = Queen/King = ist eine Karte, die an einen noch höheren Umsatz gebunden ist
Level 5 = Profesional = Ist eine Karte, die nur an gewerbliche Kunden herausgegeben wird.
Die Kundenkarte wird auf eine NFC Karte gedruckt,
Folgende Elemente soll die Kundenkarte beinhalten:
Vorderseite der Karte:
Vorname und Nachname des Kunden
Kundennummer
Kartennummer
Kundennummer als QR Code
Gültigkeit bis MM/JJJJ
Foto des Kunden
Rückseite der Karte
Unterschriftsfeld
Sicherheitscode soll auf der Rückseite

```html
<!DOCTYPE html>
<html lang="de">
<head>
<meta charset="UTF-8">
<title>Kundenkarte Level 2</title>
<link rel="stylesheet" href="https://fonts.googleapis.com/css2?family=PT+Sans:wght@400&family=Montserrat:wght@400;500&family=Caveat:wght@400&display=swap">
<style>
  :root {
    --paper: #ffffff;
    --ink: #111111;
    --card-black: #000000;
    --gold: #b89566;
    --silhouette-faint: #e4e4e6;
    --peach: #f5b28b;
    --photo-warm: #a0705a;
    --photo-dark: #2a1d18;
  }
  * { margin: 0; padding: 0; box-sizing: border-box; }
  html, body { width: 849px; height: 1200px; overflow: hidden; background: var(--paper); }
  .sheet { position: relative; width: 849px; height: 1200px; font-family: "PT Sans", sans-serif; color: var(--ink); }
  .sheet-label { position: absolute; left: 46px; top: 30px; font-size: 16px; line-height: 21px; }

  .card { position: absolute; width: 348px; height: 226px; border-radius: 21px; overflow: hidden; }

  .card-front { left: 390px; top: 135px; background: var(--card-black); }
  .front-portrait {
    position: absolute; left: 0; top: 0; width: 146px; height: 100%;
    background: linear-gradient(90deg, #ffffff 0%, #8a8a8a 45%, #000000 100%);
  }
  .front-brand {
    position: absolute; right: 22px; top: 32px;
    font-family: "Montserrat", sans-serif; font-weight: 400; font-size: 30px;
    color: #ffffff; letter-spacing: 0.5px;
  }
  .front-tier {
    position: absolute; right: 24px; top: 146px; text-align: right;
    font-family: "Caveat", cursive; font-size: 27px; line-height: 27px; color: var(--gold);
  }

  .card-back { left: 392px; top: 439px; background: var(--paper); border: 1.5px solid var(--ink); }
  .back-watermark {
    position: absolute; left: 0; top: 0; width: 144px; height: 100%;
    background: linear-gradient(180deg, #ededee 0%, var(--silhouette-faint) 100%);
  }
  .back-brand {
    position: absolute; left: 17px; top: 22px;
    font-family: "Montserrat", sans-serif; font-weight: 400; font-size: 28px; color: var(--ink);
  }
  .holder-name {
    position: absolute; left: 15px; top: 94px;
    font-family: "Montserrat", sans-serif; font-weight: 500; font-size: 16px; line-height: 22px;
  }
  .holder-data {
    position: absolute; left: 15px; top: 148px;
    font-family: "Montserrat", sans-serif; font-size: 10.5px; line-height: 17px;
  }
  .holder-photo {
    position: absolute; left: 226px; top: 22px; width: 101px; height: 120px;
    background: radial-gradient(ellipse at 50% 48%, var(--photo-warm) 0%, #7a5040 45%, var(--photo-dark) 80%, #f3f3f3 100%);
  }
  .validity {
    position: absolute; right: 17px; top: 156px; text-align: right;
    font-family: "Montserrat", sans-serif; font-size: 10px; line-height: 14px;
  }
  .signature-bar {
    position: absolute; left: 155px; bottom: 0; width: 174px; height: 33px;
    background: var(--peach); border-radius: 8px 8px 0 0;
  }
</style>
</head>
<body>
<main class="sheet">
  <p class="sheet-label">GB_Kundenkarte_Version 3<br>L2</p>

  <section class="card card-front" aria-label="Kartenvorderseite">
    <div class="front-portrait" role="img" aria-label="Schwarz-weiße Silhouette einer Frau mit lockigem Haar"></div>
    <p class="front-brand">Amara-Lumi</p>
    <p class="front-tier">Premium<br>Member Card</p>
  </section>

  <section class="card card-back" aria-label="Kartenrückseite">
    <div class="back-watermark" role="img" aria-label="Blasse graue Silhouette einer Frau als Hintergrund"></div>
    <p class="back-brand">Amara-Lumi</p>
    <p class="holder-name">Loredane<br>Musterlady</p>
    <p class="holder-data">Kundennr.: xxxxxxxxxxxxxx<br>CODE: XAIAG MAEIG</p>
    <div class="holder-photo" role="img" aria-label="Porträtfoto der Karteninhaberin"></div>
    <p class="validity">Gültig bis: xx 20xx<br>Sicherheitscode: xxxxxxxxxx</p>
    <div class="signature-bar" aria-label="Unterschriftsfeld"></div>
  </section>
</main>
</body>
</html>
```